Landing Page and Logo for Auto-Blogging Platform

I created a platform that allows users to start a blog for their business, hobby, charity, etc. I need a landing page where users can learn about the platform, benefits of consistent blogging, SEO value, plans/pricing, etc. The landing page needs to have multiple call to action buttons encouraging the visitor to register/sign up for a free trial.

In addition to the landing page, I need a page for users to establish the settings for their blog. This page should be a fairly simple form, intended for the user to enter a few details to set up their blog:
1. Name of Blog
2. Up to 10 topics and/or keywords the blog should focus on
3. Theme: Color-scheme and logo upload for blog.

I have attached the specifications of the platform's functionality so you can better understand how it works, plans/pricing, etc.

I also need a logo for the business. The name of the platform is PostNook.

Target Market(s)

Website owners, bloggers, business owners

Industry/Entity Type

Technology, Internet, web design

Coding

Coded - Design and coding required

Number of Pages Required

2 page

Colors
0054AA
0677BA
7BADD7
CADEEF
E8F1F8
0094D4
00A9DD
6FCCEA
C7EBF8
E9F6FB

Requirements
Must have
• Eye-catching design but fairly light on content (keep it simple and brief.)
Nice to have
• Eye-catching yet simple design, clean and easy to understand what we are offering.
Should not have
• Too much “wordy” and confusing content.

```html
<!DOCTYPE html>
<html lang="en">
<head>
<meta charset="utf-8">
<title>PostNook – Automate Your Blog Posting with AI</title>
<link href="https://fonts.googleapis.com/css2?family=Lato:ital,wght@0,400;0,700;0,900;1,400&family=Montserrat:wght@400;500;600;700&display=swap" rel="stylesheet">
<style>
:root{
  --blue:#0054AA;
  --blue-mid:#0677BA;
  --blue-deep:#0a5cb0;
  --sky:#7BADD7;
  --pale:#E8F1F8;
  --ink:#1d1d1f;
  --text:#444;
  --grey-bg:#f4f4f4;
  --white:#fff;
}
*{margin:0;padding:0;box-sizing:border-box}
html,body{width:1200px;height:4179px;overflow:hidden;background:var(--white)}
body{position:relative;font-family:"Lato",sans-serif;color:var(--ink)}
.abs{position:absolute}
section,header,footer{position:absolute;left:0;width:1200px}
.heading{font-family:"Montserrat",sans-serif;text-transform:uppercase;color:var(--ink);font-weight:500;white-space:nowrap}
.heading b{color:var(--blue);font-weight:700;margin-left:12px}

/* header */
.topbar{top:0;height:68px;background:var(--blue-mid)}
.navbar{top:68px;height:68px;background:var(--white);border-bottom:1px solid #e2e2e2}
.logo-box{position:absolute;left:110px;top:0;width:135px;height:136px;background:var(--white);z-index:3;text-align:center}
.logo-box .mark{position:absolute;left:42px;top:12px;width:52px;height:52px;border:4px solid var(--blue-mid);border-radius:6px}
.logo-box .name{position:absolute;left:-10px;right:-10px;top:80px;font-size:32px;font-weight:700;color:var(--blue-mid);white-space:nowrap}
.top-mail{left:310px;top:19px;display:flex;align-items:center;gap:16px;color:var(--white);font-family:"Montserrat",sans-serif;font-size:16px}
.top-mail .ico{width:30px;height:30px;border-radius:50%;background:var(--white);display:flex;align-items:center;justify-content:center}
.social{top:20px;left:610px;display:flex;gap:9px}
.social span{width:29px;height:29px;border-radius:50%;background:var(--white)}
.search{left:806px;top:13px;width:282px;height:41px;background:var(--white);display:flex}
.search .btn{width:40px;height:41px;background:#15467d;display:flex;align-items:center;justify-content:center}
.search .field{padding-left:24px;line-height:41px;font-size:13px;color:#555}
.nav{top:68px;left:311px;height:68px;display:flex;align-items:center;font-size:14.5px;color:#333}
.nav a{color:inherit;text-decoration:none;position:absolute;white-space:nowrap}
.nav .active{color:var(--blue-mid)}
.nav .active::before{content:"";position:absolute;left:-4px;right:-4px;top:-18px;height:2px;background:var(--blue-mid)}
.nav-cta{left:960px;top:84px;width:128px;height:36px;background:var(--blue);color:var(--white);font-weight:700;font-size:16px;display:flex;align-items:center;justify-content:center;border-radius:2px}

/* hero */
.hero{top:136px;height:626px;background:linear-gradient(100deg,#1f2327 0%,#2e3842 40%,#4c6a86 75%,#6f8ea8 100%)}
.hero h1{position:absolute;left:110px;top:132px;font-family:"Montserrat",sans-serif;font-weight:600;font-size:41px;line-height:60px;color:var(--white);text-shadow:0 2px 4px rgba(0,0,0,.4);white-space:nowrap}
.hero p{position:absolute;left:110px;top:262px;width:520px;font-size:16.5px;line-height:31px;color:var(--white);white-space:nowrap}
.btn-light{position:absolute;background:var(--white);color:var(--blue);font-weight:900;font-size:15px;display:flex;align-items:center;justify-content:center;border-radius:3px}
.btn-blue{position:absolute;background:var(--blue);color:var(--white);font-weight:900;font-size:15px;display:flex;align-items:center;justify-content:center;border-radius:3px}

/* about */
.about{top:762px;height:504px}
.about .visual{position:absolute;left:0;top:40px;width:540px;height:464px;background:radial-gradient(circle at 50% 55%,#dfe9f3 0%,#f4f7fa 60%,#fff 100%)}
.about h2{position:absolute;left:598px;top:82px;font-size:30px}
.about h2 b{font-size:40px}
.about .lead{position:absolute;left:598px;top:146px;font-size:19.5px;line-height:33px;color:#222;white-space:nowrap}
.about .body{position:absolute;left:598px;top:262px;font-size:15.5px;line-height:31px;color:#555;white-space:nowrap}

/* methods */
.methods{top:1266px;height:432px;background:linear-gradient(90deg,#0a56a8 0%,#0b5db2 55%,#2a73bd 75%,#0a5cb0 100%)}
.methods h2{position:absolute;left:110px;top:66px;font-size:30px;color:var(--white)}
.methods h2 b{color:var(--white);font-size:38px}
.methods ul{list-style:none;position:absolute;left:110px;top:134px;width:600px;color:var(--white);font-size:16px;line-height:31px}
.methods li{position:relative;padding-left:45px;margin-bottom:16px;white-space:nowrap}
.methods li svg{position:absolute;left:0;top:10px}
.methods li.wrap{padding-left:0;text-indent:45px}

/* how it works */
.how{top:1698px;height:819px}
.how h2{position:absolute;left:0;right:0;top:58px;text-align:center;font-size:30px}
.how h2 b{font-size:40px}
.how .intro{position:absolute;left:150px;width:900px;top:120px;text-align:center;font-size:16px;line-height:31px;color:#444}
.dots{position:absolute;width:146px;height:146px;background-image:radial-gradient(circle,#0677BA 1.6px,transparent 2px);background-size:14.6px 14.6px}
.how .photo{position:absolute;left:110px;top:215px;width:435px;height:527px;border-radius:30px;background:linear-gradient(160deg,#dfe6ea 0%,#b9c5cc 45%,#8e9aa3 100%)}
.step-ring{position:absolute;width:88px;height:88px;border-radius:50%;border:3px solid var(--blue);background:var(--white);display:flex;align-items:center;justify-content:center}
.badge{position:absolute;width:30px;height:30px;border-radius:50%;background:var(--blue);color:var(--white);font-weight:700;font-size:16px;display:flex;align-items:center;justify-content:center}
.step-title{position:absolute;font-size:21px;line-height:26px;color:#333;white-space:nowrap}
.step-sub{position:absolute;font-size:16px;line-height:28px;color:#444;white-space:nowrap}

/* pricing */
.pricing{top:2517px;height:569px;background:var(--grey-bg)}
.pricing h2{position:absolute;left:0;right:0;top:66px;text-align:center;font-size:30px}
.pricing h2 b{font-size:40px}
.plan{position:absolute;background:var(--white);box-shadow:0 4px 18px rgba(0,0,0,.08);border-radius:6px;text-align:center}
.plan h3{font-family:"Montserrat",sans-serif;font-weight:600;font-size:28px;color:var(--blue);margin-top:28px;white-space:nowrap}
.plan .per{font-size:13px;font-style:italic;font-weight:700;color:#333;margin-top:6px}
.plan .price{font-family:"Montserrat",sans-serif;font-weight:700;font-size:29px;color:var(--blue);margin-top:12px}
.plan .price small{font-size:22px}
.plan hr{border:0;border-top:1px solid #bbb;margin:16px 0 12px}
.plan .feat{font-size:14px;line-height:26px;color:#333}
.plan .learn{display:inline-block;margin-top:16px;width:125px;height:29px;line-height:29px;background:var(--blue);color:var(--white);font-size:14px;font-weight:700}
.plan.featured{background:var(--blue);z-index:2;box-shadow:0 8px 24px rgba(0,40,100,.25)}
.plan.featured h3,.plan.featured .per,.plan.featured .price,.plan.featured .feat{color:var(--white)}
.plan.featured hr{border-top-color:rgba(255,255,255,.6)}
.plan.featured .learn{background:var(--white);color:var(--blue)}

/* contact */
.contact{top:3086px;height:624px}
.contact .panel{position:absolute;left:117px;top:70px;width:447px;height:384px;border-radius:20px 0 0 0;background:linear-gradient(135deg,#0a5cb0,#0c63b8 60%,#1a6fc0)}
.contact .panel .label{position:absolute;right:139px;top:105px;font-family:"Montserrat",sans-serif;font-weight:600;font-size:18px;color:var(--white);text-align:right}
.contact .panel .big{position:absolute;right:139px;top:132px;text-align:right;color:var(--white);font-family:"Montserrat",sans-serif;font-size:38px;line-height:44px;font-weight:500}
.contact .panel .big strong{font-weight:700}
.contact .panel .big span{font-weight:400}
.contact .frame{position:absolute;left:749px;top:89px;width:367px;height:347px;border:4px solid var(--blue)}
.form-card{position:absolute;left:470px;top:121px;width:625px;height:433px;background:var(--white);border-radius:20px;box-shadow:0 6px 30px rgba(0,0,0,.1)}
.form-card h2{position:absolute;left:52px;top:32px;font-size:30px}
.form-card h2 b{font-size:38px}
.fld{position:absolute;width:227px}
.fld label{display:block;font-size:14.5px;font-weight:700;color:#222}
.fld .val{font-size:12px;color:#888;margin-top:14px;padding-bottom:10px;border-bottom:1px solid #ccc;white-space:nowrap}
.send{position:absolute;left:502px;top:325px;width:64px;height:64px;border-radius:50%;background:var(--blue);display:flex;align-items:center;justify-content:center}

/* footer */
.site-footer{top:3710px;height:469px;background:var(--blue-deep);color:var(--white)}
.f-logo{position:absolute;left:110px;top:44px;display:flex;align-items:center;gap:14px}
.f-logo .mark{width:56px;height:56px;border:3px solid var(--white);border-radius:6px}
.f-logo .name{font-size:34px;font-weight:700}
.f-sep{position:absolute;left:350px;top:48px;width:2px;height:50px;background:var(--white)}
.news{position:absolute;left:379px;top:60px;font-family:"Montserrat",sans-serif;font-weight:600;font-size:25px;white-space:nowrap}
.news-input{position:absolute;left:696px;top:50px;width:188px;height:48px;border:1px solid rgba(255,255,255,.8);font-size:11px;padding-left:8px;line-height:46px}
.news-btn{position:absolute;left:902px;top:50px;width:186px;height:48px;background:var(--white);color:var(--blue);font-family:"Montserrat",sans-serif;font-weight:600;font-size:17px;display:flex;align-items:center;justify-content:center;gap:40px}
.f-rule{position:absolute;left:110px;width:978px;height:1px;background:rgba(255,255,255,.7)}
.f-col h4{position:absolute;top:172px;font-family:"Montserrat",sans-serif;font-weight:700;font-size:24px}
.f-list{position:absolute;font-family:"Montserrat",sans-serif;font-size:16px;letter-spacing:.4px}
.f-list div{position:absolute;white-space:nowrap;display:flex;align-items:center;gap:10px}
.copy{position:absolute;left:0;right:0;top:431px;text-align:center;font-family:"Montserrat",sans-serif;font-size:15px}
</style>
</head>
<body>

<header class="topbar">
  <div class="abs top-mail"><span class="ico"><svg width="16" height="12" viewBox="0 0 16 12"><rect x="0" y="0" width="16" height="12" rx="2" fill="#0677BA"/><path d="M1 1 8 7 15 1" stroke="#fff" stroke-width="1.6" fill="none"/></svg></span>hello@postnook.example</div>
  <div class="abs social"><span></span><span></span><span></span><span></span></div>
  <div class="abs search"><div class="btn"><svg width="18" height="18" viewBox="0 0 18 18"><circle cx="7.5" cy="7.5" r="5.5" stroke="#fff" stroke-width="2.2" fill="none"/><path d="M11.5 11.5 16 16" stroke="#fff" stroke-width="2.4"/></svg></div><div class="field">Search.......</div></div>
</header>
<div class="abs navbar" style="left:0;width:1200px"></div>
<div class="logo-box"><span class="mark"></span><span class="name">PostNook</span></div>
<nav class="abs nav">
  <a class="active" style="left:0">Home</a>
  <a style="left:99px">About Us</a>
  <a style="left:223px">Our Benefits</a>
  <a style="left:372px">Subscription Plan</a>
  <a style="left:552px">Latest Blog</a>
</nav>
<div class="abs nav-cta">CONTACT</div>

<section class="hero" role="img" aria-label="Photo of two men working at a computer in an office">
  <h1>AUTOMATE YOUR BLOG<br>POSTING WITH AI.</h1>
  <p>Transform your blogging experience with our AI-powered plat-<br>form that not only generates and optimizes content tailored to<br>your audience but also continuously learns and adapts to deliver<br>smarter insights, ensuring your voice stands out in a crowded<br>digital landscape.</p>
  <div class="btn-light" style="left:110px;top:440px;width:245px;height:45px">SIGN UP FOR A FREE TRIAL</div>
</section>

<section class="about">
  <div class="visual" role="img" aria-label="Illustration of a woman holding a laptop showing charts"></div>
  <h2 class="heading">About<b>US</b></h2>
  <p class="lead">The purpose of this platform is to allow anyone to<br>start a blog and automate the process &nbsp;of creating<br>content and posting it to the blog</p>
  <p class="body">Lorem ipsum dolor sit amet, consectetur adipiscing elit, sed do<br>eiusmod tempor incididunt ut labore et dolore magna aliqua. Ut<br>enim ad minim veniam, quis nostrud exercitation ullamco laboris<br>nisi ut aliquip ex ea commodo consequat.</p>
  <div class="btn-blue" style="left:598px;top:412px;width:167px;height:39px">READ MORE</div>
</section>

<section class="methods" role="img" aria-label="Blue-tinted photo of a person working on a laptop">
  <h2 class="heading">Our<b>METHODS</b></h2>
  <ul>
    <li><svg width="22" height="10" viewBox="0 0 22 10"><path d="M0 5h19M15 1l5 4-5 4" stroke="#fff" stroke-width="2" fill="none"/></svg>The user enters them into a table manually.</li>
    <li><svg width="22" height="10" viewBox="0 0 22 10"><path d="M0 5h19M15 1l5 4-5 4" stroke="#fff" stroke-width="2" fill="none"/></svg>The user uploads a list of blog topics in CSV format.</li>
    <li class="wrap"><svg width="22" height="10" viewBox="0 0 22 10" style="left:0"><path d="M0 5h19M15 1l5 4-5 4" stroke="#fff" stroke-width="2" fill="none"/></svg>AI can create the list of blog topics based on a prompt such as:<br><span style="display:inline-block;text-indent:0">“Provide a list of 52 &nbsp;blog topics for a handyman business’s blog.”</span></li>
  </ul>
  <div class="btn-light" style="left:110px;top:323px;width:167px;height:39px">REGISTER</div>
</section>

<section class="how">
  <h2 class="heading">How it<b>WORKS</b></h2>
  <p class="intro">Lorem ipsum dolor sit amet, consecteur adipiscing elit, sed do eiusmod tempor incididunt ut labore et dolore<br>magna aliqua. Ut enim ad minim veniam,</p>
  <div class="dots" style="left:81px;top:170px"></div>
  <div class="photo" role="img" aria-label="Photo of a smiling woman holding a tablet"></div>

  <svg class="abs" style="left:600px;top:240px" width="160" height="500" viewBox="0 0 160 500">
    <path d="M45 50 C40 80 50 95 72 105" stroke="#555" stroke-width="1.2" stroke-dasharray="4 4" fill="none"/>
    <path d="M75 200 C75 225 65 235 55 250" stroke="#555" stroke-width="1.2" stroke-dasharray="4 4" fill="none"/>
    <path d="M45 345 C40 370 52 385 72 395" stroke="#555" stroke-width="1.2" stroke-dasharray="4 4" fill="none"/>
  </svg>

  <div class="step-ring" style="left:618px;top:217px"><svg width="34" height="32" viewBox="0 0 34 32"><rect x="2" y="3" width="30" height="27" rx="3" stroke="#1d1d1f" stroke-width="2.2" fill="none"/><path d="M2 10h30" stroke="#1d1d1f" stroke-width="2.2"/><rect x="8" y="14" width="18" height="3" fill="#0054AA"/><rect x="8" y="20" width="18" height="3" fill="#0054AA"/></svg></div>
  <div class="badge" style="left:601px;top:236px">1</div>
  <div class="step-title" style="left:726px;top:215px">Select frequency of Automated<br>Blog Posts</div>
  <div class="step-sub" style="left:726px;top:281px">Daily, Weekly, Monthly</div>

  <div class="step-ring" style="left:627px;top:363px"><svg width="40" height="26" viewBox="0 0 40 26"><path d="M2 8l8-4 10 6 10-6 8 4-10 14-8-6-8 6z" stroke="#1d1d1f" stroke-width="2" fill="#cadeef"/></svg></div>
  <div class="badge" style="left:698px;top:374px">2</div>
  <div class="step-title" style="left:741px;top:361px">Name your blog Step</div>
  <div class="step-sub" style="left:741px;top:402px">Lorem ipsum dolor sit amet, consectetur<br>adipiscing elit.</div>

  <div class="step-ring" style="left:618px;top:507px"><svg width="36" height="32" viewBox="0 0 36 32"><rect x="2" y="3" width="28" height="24" rx="3" stroke="#1d1d1f" stroke-width="2.2" fill="none"/><path d="M2 9h28" stroke="#1d1d1f" stroke-width="2.2"/><path d="M18 26l12-12 4 4-12 12h-4z" fill="#0054AA"/></svg></div>
  <div class="badge" style="left:603px;top:526px">3</div>
  <div class="step-title" style="left:726px;top:505px">Select your blog topics</div>
  <div class="step-sub" style="left:726px;top:547px">let AI choose them for you</div>

  <div class="step-ring" style="left:627px;top:655px"><svg width="30" height="34" viewBox="0 0 30 34"><path d="M4 14h6v17H4zM10 16l6-12c3 0 4 2 3 6l-1 4h8c2 0 3 2 2 4l-4 11c-1 2-2 2-4 2H10z" stroke="#1d1d1f" stroke-width="2" fill="#cadeef"/></svg></div>
  <div class="badge" style="left:698px;top:664px">4</div>
  <div class="step-title" style="left:736px;top:652px">Go do something else and let AI<br>do all your blogging for you!</div>
  <div class="step-sub" style="left:736px;top:719px">Daily, Weekly, Monthly</div>
</section>

<section class="pricing">
  <h2 class="heading">Our<b>PRICING</b></h2>
  <div class="plan" style="left:185px;top:176px;width:282px;height:312px">
    <h3>BASE PLAN</h3><div class="per">Every month:</div>
    <div class="price">$9.99<small>/mo.</small></div><hr>
    <div class="feat">1 blog post (up to 2,000 words)<br>every month:</div>
    <div class="learn">Learn More</div>
  </div>
  <div class="plan featured" style="left:451px;top:142px;width:295px;height:328px">
    <h3>PREMIUM PLAN</h3><div class="per">Every week:</div>
    <div class="price">$14.99<small>/mo.</small></div><hr>
    <div class="feat">1 blog post (up to 2,000 words)<br>every week;</div>
    <div class="learn">Learn More</div>
  </div>
  <div class="plan" style="left:733px;top:176px;width:282px;height:312px">
    <h3>ULTIMATE PLAN</h3><div class="per">Every month:</div>
    <div class="price">$24<small>/mo.</small></div><hr>
    <div class="feat">1 blog post per day plus unlimited<br>manual &nbsp;posting</div>
    <div class="learn">Learn More</div>
  </div>
</section>

<section class="contact">
  <div class="panel" role="img" aria-label="Blue-tinted photo of a person typing on a laptop">
    <div class="label">CONTACT US</div>
    <div class="big"><strong>Let’s Do</strong><br><span>Good</span><br>Together!</div>
  </div>
  <div class="dots" style="left:81px;top:352px"></div>
  <div class="frame"></div>
  <div class="form-card">
    <h2 class="heading">Send us<b>A MESSAGE</b></h2>
    <div class="fld" style="left:57px;top:110px"><label>Your Name</label><div class="val">PostNook</div></div>
    <div class="fld" style="left:333px;top:110px"><label>Company</label><div class="val">Lorem ipsum dolor sit amet</div></div>
    <div class="fld" style="left:57px;top:203px"><label>Email Address</label><div class="val">hello@postnook.example</div></div>
    <div class="fld" style="left:333px;top:203px"><label>Phone</label><div class="val">+1 555 014 2270</div></div>
    <div class="fld" style="left:57px;top:297px;width:446px"><label>Message</label><div class="val" style="padding-bottom:36px">Lorem ipsum dolor sit amet, consectetur adipiscing elit.</div></div>
    <div class="send"><svg width="24" height="24" viewBox="0 0 24 24"><path d="M22 2 2 10l8 3 3 8z" fill="#fff"/><path d="M22 2 10 13" stroke="#0054AA" stroke-width="1.5"/></svg></div>
  </div>
</section>

<footer class="site-footer">
  <div class="f-logo"><span class="mark"></span><span class="name">PostNook</span></div>
  <div class="f-sep"></div>
  <div class="news">Newsletter Subscription</div>
  <div class="news-input">Enter Your E-mail</div>
  <div class="news-btn">SUBSCRIBE <svg width="18" height="14" viewBox="0 0 18 14"><rect width="18" height="14" rx="2" fill="#0054AA"/><path d="M1 1 9 8 17 1" stroke="#fff" stroke-width="1.6" fill="none"/></svg></div>
  <div class="f-rule" style="top:135px"></div>

  <div class="f-col"><h4 style="left:112px">CONTACT US</h4><h4 style="left:546px">QUICK LINKS</h4><h4 style="left:927px">ABOUT INFO</h4></div>

  <div class="f-list" style="left:113px;top:0">
    <div style="top:241px"><svg width="14" height="18" viewBox="0 0 14 18"><path d="M7 17C2 10 1 8 1 6a6 6 0 0 1 12 0c0 2-1 4-6 11z" fill="#fff"/><circle cx="7" cy="6" r="2.3" fill="#0a5cb0"/></svg><span style="margin-left:8px">United States, PostNook.</span></div>
    <div style="top:288px"><svg width="16" height="16" viewBox="0 0 16 16"><path d="M3 1l3 3-2 2c1 3 3 5 6 6l2-2 3 3-2 2C7 15 1 9 1 3z" fill="#fff"/></svg><span style="margin-left:8px">+1 555 014 2270</span></div>
    <div style="top:335px"><svg width="18" height="14" viewBox="0 0 18 14"><rect width="18" height="14" rx="2" fill="#fff"/><path d="M1 1 9 8 17 1" stroke="#0a5cb0" stroke-width="1.6" fill="none"/></svg><span style="margin-left:8px">hello@postnook.example</span></div>
  </div>

  <div class="f-list" style="left:546px;top:0">
    <div style="top:228px"><svg width="16" height="8" viewBox="0 0 16 8"><path d="M0 4h13M10 1l4 3-4 3" stroke="#fff" stroke-width="1.6" fill="none"/></svg>Terms of Service</div>
    <div style="top:262px"><svg width="16" height="8" viewBox="0 0 16 8"><path d="M0 4h13M10 1l4 3-4 3" stroke="#fff" stroke-width="1.6" fill="none"/></svg>Returns Policy</div>
    <div style="top:296px"><svg width="16" height="8" viewBox="0 0 16 8"><path d="M0 4h13M10 1l4 3-4 3" stroke="#fff" stroke-width="1.6" fill="none"/></svg>Our Products</div>
    <div style="top:330px"><svg width="16" height="8" viewBox="0 0 16 8"><path d="M0 4h13M10 1l4 3-4 3" stroke="#fff" stroke-width="1.6" fill="none"/></svg>Contact</div>
    <div style="top:364px"><svg width="16" height="8" viewBox="0 0 16 8"><path d="M0 4h13M10 1l4 3-4 3" stroke="#fff" stroke-width="1.6" fill="none"/></svg>Privacy Policy</div>
  </div>

  <div class="f-list" style="left:926px;top:0">
    <div style="top:228px"><svg width="16" height="8" viewBox="0 0 16 8"><path d="M0 4h13M10 1l4 3-4 3" stroke="#fff" stroke-width="1.6" fill="none"/></svg>Home</div>
    <div style="top:262px"><svg width="16" height="8" viewBox="0 0 16 8"><path d="M0 4h13M10 1l4 3-4 3" stroke="#fff" stroke-width="1.6" fill="none"/></svg>About Us</div>
    <div style="top:296px"><svg width="16" height="8" viewBox="0 0 16 8"><path d="M0 4h13M10 1l4 3-4 3" stroke="#fff" stroke-width="1.6" fill="none"/></svg>Our Benifits</div>
    <div style="top:330px"><svg width="16" height="8" viewBox="0 0 16 8"><path d="M0 4h13M10 1l4 3-4 3" stroke="#fff" stroke-width="1.6" fill="none"/></svg>Subscription plan</div>
    <div style="top:364px"><svg width="16" height="8" viewBox="0 0 16 8"><path d="M0 4h13M10 1l4 3-4 3" stroke="#fff" stroke-width="1.6" fill="none"/></svg>Latest Blog</div>
  </div>

  <div class="f-rule" style="top:410px"></div>
  <div class="copy">Copyright © 2024 PostNook. All rights reserved.</div>
</footer>

</body>
</html>
```